Tall Fern Roofing Business Card

Need a business card with the logo that was designed here

Contact Information for Business Card

Name, Title, Phone, Email, Website, Company name

```html
<!DOCTYPE html>
<html lang="en">
<head>
<meta charset="utf-8">
<title>Tall Fern Roofing Business Card</title>
<link rel="stylesheet" href="https://fonts.googleapis.com/css2?family=Montserrat:wght@400;500;700&display=swap">
<style>
  :root {
    --brand-blue: #4072b8;
    --card-white: #ffffff;
    --text-grey: #6f6f6f;
    --stage-top: #d2d2d2;
    --stage-bottom: #a3a3a3;
  }
  * { box-sizing: border-box; margin: 0; padding: 0; }
  html, body { width: 1200px; height: 802px; overflow: hidden; }
  body {
    background: linear-gradient(180deg, var(--stage-top), var(--stage-bottom));
    font-family: "Montserrat", Arial, sans-serif;
    position: relative;
  }
  .card {
    position: absolute;
    top: 251px;
    width: 525px;
    height: 300px;
    border-radius: 22px;
    overflow: hidden;
    box-shadow: 0 14px 30px rgba(0,0,0,0.28);
  }
  .card-front { left: 50px; background: var(--card-white); }
  .card-back { left: 625px; background: var(--brand-blue); display: flex; align-items: center; justify-content: center; }

  .front-band { position: absolute; inset: 0; width: 100%; height: 100%; }
  .front-band .band-fill { fill: var(--brand-blue); }
  .front-band .band-stripe { fill: none; stroke: var(--brand-blue); stroke-width: 6; }

  .holder { position: absolute; left: 34px; top: 34px; color: var(--card-white); }
  .holder-name { font-weight: 700; font-size: 21px; letter-spacing: 1px; text-transform: uppercase; }
  .holder-title { font-weight: 400; font-size: 13px; margin-top: 3px; }

  .front-brand {
    position: absolute; right: 36px; top: 100px; width: 190px;
    color: var(--brand-blue); font-weight: 700; font-size: 26px; line-height: 1.1; text-align: center;
  }

  .contact { position: absolute; left: 40px; top: 170px; color: var(--text-grey); font-size: 13px; line-height: 1.5; }
  .contact-address { margin-bottom: 12px; }
  .contact-line { display: flex; align-items: center; gap: 8px; }
  .contact-line svg { width: 11px; height: 11px; flex: none; }
  .contact-line svg .icon { fill: var(--brand-blue); }

  .back-brand { color: var(--card-white); font-weight: 700; font-size: 40px; text-align: center; line-height: 1.1; }
</style>
</head>
<body>
  <section class="card card-front" aria-label="Business card front">
    <svg class="front-band" viewBox="0 0 525 300" aria-hidden="true">
      <polygon class="band-fill" points="0,0 330,0 282,104 0,104"/>
      <polyline class="band-stripe" points="0,122 292,122 348,0"/>
    </svg>
    <div class="holder">
      <div class="holder-name">Darren Whitley</div>
      <div class="holder-title">Managing Director</div>
    </div>
    <div class="front-brand">Tall Fern Roofing</div>
    <div class="contact">
      <div class="contact-address">418 W Harlow Avenue<br>Marston County Vale 6184</div>
      <div class="contact-line">
        <svg viewBox="0 0 12 12"><path class="icon" d="M2 1l2 0 1 3-1.3 1a7 7 0 0 0 3.3 3.3L8 7l3 1v2a1 1 0 0 1-1 1A9 9 0 0 1 1 2a1 1 0 0 1 1-1z"/></svg>
        <span>0491 555 027</span>
      </div>
      <div class="contact-line">
        <svg viewBox="0 0 12 12"><path class="icon" d="M1 2h10v8H1z M1 2l5 4 5-4" /></svg>
        <span>info@tallfernroofing.com</span>
      </div>
      <div class="contact-line">
        <svg viewBox="0 0 12 12"><circle class="icon" cx="6" cy="6" r="5"/></svg>
        <span>www.tallfernroofing.com</span>
      </div>
    </div>
  </section>

  <section class="card card-back" aria-label="Business card back">
    <div class="back-brand">Tall Fern Roofing</div>
  </section>
</body>
</html>
```